Casino with the 'highest winning percentage' needs a stationery design

This is for a casino in Colombo, Sri Lanka and we need a stationery design for business card, letter head and envelope.

Should be very professional, simple and elegant without fancy fonts

Reason: Not fully satisfied with the designs. Need more designs.

Business

• 1. card deck symbol 'CLUBS' in red, or black

2. name in BLOCK CAPITAL LETTERS

3. Preferred font colours are black, white or red

4. Prefer 'professional /elegant' fonts
• SHOULD NOT HAVE ANY OTHER SYMBOL EXCEPT 'CLUBS'

DO NOT PREFER ITALIC FONTS

```html
<!DOCTYPE html>
<html lang="en">
<head>
<meta charset="utf-8">
<title>Halvern Gaming Stationery</title>
<link href="https://fonts.googleapis.com/css2?family=Noto+Serif:wght@700&family=Open+Sans:wght@400;600&display=swap" rel="stylesheet">
<style>
:root{
  --red:#d3303b;
  --ink:#1d1d1d;
  --grey:#555;
  --paper:#ffffff;
  --paper-shade:#eeeeee;
  --backdrop:#e9e4de;
  --rule:#333;
  --label:#9a8f84;
}
*{box-sizing:border-box;margin:0;padding:0}
html,body{width:1200px;height:387px;overflow:hidden;background:var(--backdrop)}
body{position:relative;font-family:"Open Sans",Arial,sans-serif;color:var(--ink)}
.sheet{position:absolute;top:22px;width:260px;height:338px;background:linear-gradient(180deg,var(--paper) 0%,var(--paper-shade) 100%);box-shadow:0 1px 4px rgba(0,0,0,.25)}
.brand{position:absolute;display:flex;align-items:center;gap:6px;white-space:nowrap}
.brand-dot{width:22px;height:22px;border-radius:50%;background:var(--red);flex:none}
.brand-name{font-family:"Open Sans",Arial,sans-serif;font-weight:600;font-size:10px;line-height:12px;color:var(--ink);letter-spacing:.6px}
.contact{position:absolute;font-size:4.2px;line-height:6px;color:var(--grey);white-space:nowrap}
.contact .co{color:var(--red)}
.band{position:absolute;left:0;right:0;bottom:0;height:10px;background:var(--red);color:#fff;font-size:4.6px;letter-spacing:.9px;text-align:center;line-height:10px;white-space:nowrap}
.band::before{content:"";position:absolute;left:0;right:0;top:-3px;height:.6px;background:var(--rule)}
.label{position:absolute;top:360px;font-size:19px;color:var(--label);width:260px;text-align:center;line-height:24px}

/* option 1 */
.opt1{left:8px}
.opt1 .brand{left:76px;top:12px}
.suit-field{position:absolute;left:50px;top:82px;width:174px;height:164px;border-radius:6px;background:linear-gradient(135deg,rgba(0,0,0,.04),rgba(211,48,59,.06) 50%,rgba(0,0,0,.07))}
.opt1 .footer{position:absolute;left:0;right:0;top:323px;text-align:center;font-size:4.3px;line-height:7px;color:var(--grey);white-space:nowrap}
.opt1 .footer .co{color:var(--red)}

/* option 2 */
.opt2{left:284px}
.opt2 .brand{left:12px;top:12px}
.opt2 .contact{left:192px;top:8px}

/* option 3 */
.opt3{left:558px}
.opt3 .brand{left:12px;top:12px}
.opt3 .contact{left:192px;top:8px}
.fax-title{position:absolute;left:10px;top:76px;font-size:19px;letter-spacing:1px}
.fax-field{position:absolute;height:9px;border-bottom:.6px solid var(--rule);font-size:4.4px;line-height:7px}
.fax-field.left{left:10px;width:120px}
.fax-field.right{left:142px;width:91px}
.fax-checks{position:absolute;left:10px;top:172px;display:flex;gap:12px;font-size:4.4px;align-items:center;white-space:nowrap}
.fax-checks span{display:flex;align-items:center;gap:3px}
.fax-checks i{display:block;width:6px;height:6px;border:.6px solid var(--rule)}
.opt3 .band{font-size:4.3px;letter-spacing:.2px}

/* envelopes */
.envelope{position:absolute;background:var(--paper);box-shadow:0 1px 4px rgba(0,0,0,.25)}
.env-back{left:902px;top:0;width:298px;height:196px}
.env-open{left:838px;top:66px;width:322px;height:130px}
.env-front{left:870px;top:124px;width:292px;height:130px;background:linear-gradient(180deg,var(--paper),var(--paper-shade))}
.env-front .brand{left:12px;top:14px}
.env-front .brand-dot{width:26px;height:26px}
.env-front .brand-name{font-size:11px;line-height:13px}
.env-address{position:absolute;left:44px;top:42px;font-family:"Noto Serif",Georgia,serif;font-weight:700;font-size:5px;line-height:7px;white-space:nowrap}
.env-front .band{height:9px;line-height:9px;font-size:4.8px}

/* business cards */
.card{position:absolute;top:272px;width:158px;height:90px;box-shadow:0 1px 4px rgba(0,0,0,.25)}
.card-front{left:862px;background:var(--paper)}
.card-front .brand{left:34px;top:14px}
.card-front .brand-dot{width:20px;height:20px}
.card-front .brand-name{font-size:9px;line-height:11px}
.card-left{position:absolute;right:86px;top:47px;text-align:right;font-size:4.2px;line-height:6px;color:var(--grey);white-space:nowrap}
.card-left .co{font-weight:600;color:var(--red);font-size:5px;line-height:8px}
.card-divider{position:absolute;left:75px;top:46px;width:.6px;height:26px;background:#bbb}
.card-front .contact{left:80px;top:47px}
.card-front .band{height:7px;line-height:7px;font-size:3.8px}
.card-back{left:1029px;background:var(--red);color:#fff}
.card-back .suit-field{left:40px;top:6px;width:78px;height:22px;border-radius:4px;background:linear-gradient(90deg,rgba(255,255,255,.07),rgba(255,255,255,.12))}
.card-back .brand{left:30px;top:38px}
.card-back .brand-dot{width:20px;height:20px;background:#fff}
.card-back .brand-name{color:#fff;font-size:9px;line-height:11px}
.tagline{position:absolute;left:0;right:0;top:70px;text-align:center;font-family:"Noto Serif",Georgia,serif;font-weight:700;font-size:4.8px;letter-spacing:.4px;white-space:nowrap}
</style>
</head>
<body>

<section class="sheet opt1" aria-label="Letterhead option one">
  <div class="brand"><span class="brand-dot"></span><span class="brand-name">HALVERN GAMING</span></div>
  <div class="suit-field" role="img" aria-label="Faint playing card suit pattern in grey and red"></div>
  <div class="footer">
    <span class="co">HALVERN GAMING LTD</span> 58, Lotus Terrace Road, Colombo 01000, Sri Lanka<br>
    ✆ +94 11 2000481 &nbsp;☎ +94 11 2000482 &nbsp;✉ info@halverncolombo.com &nbsp;◎ www.halverncolombo.com
  </div>
</section>
<div class="label" style="left:8px">Option-1</div>

<section class="sheet opt2" aria-label="Letterhead option two">
  <div class="brand"><span class="brand-dot"></span><span class="brand-name">HALVERN GAMING</span></div>
  <div class="contact">✆ +94 11 2000481<br>☎ +94 11 2000482<br>✉ info@halverncolombo.com<br><span class="co">HALVERN GAMING LTD</span><br>58, Lotus Terrace Road<br>Colombo 01000, Sri Lanka</div>
  <div class="band">www.halverncolombo.com</div>
</section>
<div class="label" style="left:284px">Option-2</div>

<section class="sheet opt3" aria-label="Fax sheet option three">
  <div class="brand"><span class="brand-dot"></span><span class="brand-name">HALVERN GAMING</span></div>
  <div class="contact">✆ +94 11 2000481<br>☎ +94 11 2000482<br>✉ info@halverncolombo.com<br>◎ www.halverncolombo.com</div>
  <div class="fax-title">FAX</div>
  <div class="fax-field left" style="top:107px">To :</div>
  <div class="fax-field right" style="top:107px">From :</div>
  <div class="fax-field left" style="top:121px">Fax :</div>
  <div class="fax-field right" style="top:121px">Pages :</div>
  <div class="fax-field left" style="top:134px">Phone :</div>
  <div class="fax-field right" style="top:134px">Date :</div>
  <div class="fax-field left" style="top:148px">Re :</div>
  <div class="fax-field right" style="top:148px">CC :</div>
  <div class="fax-checks">
    <span><i></i>Urgent</span><span><i></i>For Review</span><span><i></i>Please Comment</span><span><i></i>Please Reply</span><span><i></i>Please Recycle</span>
  </div>
  <div class="band">HALVERN GAMING LTD &nbsp;58, Lotus Terrace Road, Colombo 01000, Sri Lanka</div>
</section>
<div class="label" style="left:558px">Option-3</div>

<section class="envelope env-back" aria-label="Envelope back with red flap">
  <svg width="298" height="196" viewBox="0 0 298 196" aria-hidden="true">
    <path d="M0 0H298V34Q220 48 149 60Q78 48 0 34Z" fill="var(--red)"/>
  </svg>
</section>

<section class="envelope env-open" aria-label="Envelope back with white flap">
  <svg width="322" height="130" viewBox="0 0 322 130" aria-hidden="true">
    <path d="M0 .5Q140 30 172 38Q200 30 322 .5" fill="none" stroke="var(--rule)" stroke-width=".8"/>
  </svg>
</section>

<section class="envelope env-front" aria-label="Envelope front">
  <div class="brand"><span class="brand-dot"></span><span class="brand-name">HALVERN GAMING</span></div>
  <div class="env-address">58, Lotus Terrace Road<br>Colombo 01000, Sri Lanka</div>
  <div class="band">www.halverncolombo.com</div>
</section>

<section class="card card-front" aria-label="Business card front">
  <div class="brand"><span class="brand-dot"></span><span class="brand-name">HALVERN GAMING</span></div>
  <div class="card-left"><span class="co">HALVERN GAMING LTD</span><br>58, Lotus Terrace Road<br>Colombo 01000<br>Sri Lanka</div>
  <div class="card-divider"></div>
  <div class="contact">✆ +94 11 2000481<br>☏ +94 77 2000483<br>☎ +94 11 2000482<br>✉ info@halverncolombo.com</div>
  <div class="band">www.halverncolombo.com</div>
</section>

<section class="card card-back" aria-label="Business card back">
  <div class="suit-field" role="img" aria-label="Faint playing card suit pattern"></div>
  <div class="brand"><span class="brand-dot"></span><span class="brand-name">HALVERN GAMING</span></div>
  <div class="tagline">Highest Winning Percentage In The World</div>
</section>

</body>
</html>
```